Business Intelligence / Data Visualization Firm Seeking World Class Power Point Deck

Vela Crest delivers enterprise business intelligence and data visualization solutions enabling clients to see their business as they've never seen it - we transform complex, unstructured data into simple insight that facilitates intelligent decision making, revenue growth and risk reduction. We're seeking a world class power point template for internal, client and conference presentations.

Please visit velacrest.example for more company context.
*Note: A website photo has been uploaded and may be used or not used - designer discretion.

Additional context:
We use Lumadrift: https://lumadrift.norvex.example/products/predictive-analytics.

Target Market(s)

CXOs at Meridian 100 companies | small and medium business owners (BI / data-viz experts and also decision makers who don't actually understand BI / data-viz).

Industry/Entity Type

Professional Service

Font styles to use
Sans Serif
Other font styles liked:
• Our logo is Expansiva (uploaded), our site is Tahoma. Please use your discretion,.

Colors
ec1f27
ffffff
000000

Requirements
Must have
• PPT format, editable.
• Prefer simple, clean, strong presentation.
Nice to have
• Designs that relate to data, analytics, solutions, automation and transforming complexity into simplicity.
• Reusable icons.

```html
<!DOCTYPE html>
<html lang="en">
<head>
<meta charset="utf-8">
<title>Vela Crest — Presentation Template Overview</title>
<link rel="stylesheet" href="https://fonts.googleapis.com/css2?family=Open+Sans:wght@400;600;700;800&display=swap">
<style>
:root{
  --red:#e3232b;
  --ink:#3b3b3d;
  --dark:#333335;
  --mid:#6b6b6d;
  --soft:#c9c9cb;
  --line:#e4e4e4;
  --page:#a9a9a9;
  --white:#ffffff;
}
*{box-sizing:border-box;margin:0;padding:0}
html,body{width:701px;height:1200px;overflow:hidden}
body{background:var(--page);font-family:'Open Sans',sans-serif;color:var(--ink)}
.sheet{position:absolute;left:10px;top:14px;display:grid;grid-template-columns:repeat(3,222px);grid-template-rows:repeat(9,124px);gap:7px}
.slide{position:relative;background:var(--white);overflow:hidden}
.abs{position:absolute}
.bg-city{position:absolute;inset:0;background:linear-gradient(180deg,#5a5a5c 0%,#38383a 45%,#232325 100%)}
.band-city{position:absolute;left:0;right:0;top:0;background:linear-gradient(180deg,#6a6a6c,#2f2f31)}
.brand{font-family:'Open Sans',sans-serif;font-weight:600;letter-spacing:.22em;white-space:nowrap}
.brand-light{color:var(--white)}
.brand-dark{color:var(--ink)}
.hdr{position:absolute;left:5px;top:5px;font-size:5px;font-weight:700;color:var(--ink);padding:1px 0 0 4px;border-left:1.4px solid var(--red);border-top:1.4px solid var(--red);line-height:1.2}
.foot{position:absolute;left:5px;right:6px;bottom:3px;display:flex;align-items:center;gap:3px;font-size:2.3px;color:#888}
.foot .pg{width:5px;height:5px;border-radius:50%;background:var(--red);color:#fff;font-size:2.4px;display:flex;align-items:center;justify-content:center}
.foot .brand{margin-left:auto;font-size:3.2px;color:var(--ink)}
.lo{font-size:2.5px;line-height:1.4;color:#6d6d6d}
.lo-w{font-size:2.5px;line-height:1.4;color:#d8d8d8}
.t{font-size:3.4px;font-weight:700;color:var(--ink)}
.t-red{color:var(--red)}
.pill{display:inline-block;background:var(--red);color:#fff;font-size:2.8px;font-weight:700;padding:1px 5px;border-radius:4px}
.ico{width:10px;height:10px;border-radius:50%;border:.7px solid var(--red);display:flex;align-items:center;justify-content:center;color:var(--red)}
.ico svg{width:6px;height:6px}
.ico-fill{background:var(--red);border:none;color:#fff}
.ico-dark{background:var(--dark);border:none;color:#fff}
.row{display:flex}
table{border-collapse:collapse;width:100%;font-size:2.5px;color:#555}
th{background:var(--red);color:#fff;font-weight:700;padding:1.2px 2px;text-align:left}
td{padding:1.6px 2px;border-bottom:.4px solid var(--line)}
.tbl-foot td{background:var(--mid);height:5px;border:none}
</style>
</head>
<body>
<svg width="0" height="0" style="position:absolute" aria-hidden="true">
  <symbol id="i-bars" viewBox="0 0 12 12"><path d="M1 11h10M2.5 10V6M5 10V3M7.5 10V5M10 10V2" stroke="currentColor" stroke-width="1.3" fill="none"/></symbol>
  <symbol id="i-pie" viewBox="0 0 12 12"><circle cx="6" cy="6" r="4.5" stroke="currentColor" stroke-width="1.2" fill="none"/><path d="M6 6V1.5A4.5 4.5 0 0 1 10.5 6Z" fill="currentColor"/></symbol>
  <symbol id="i-target" viewBox="0 0 12 12"><circle cx="6" cy="6" r="4.8" stroke="currentColor" stroke-width="1" fill="none"/><circle cx="6" cy="6" r="2.6" stroke="currentColor" stroke-width="1" fill="none"/><circle cx="6" cy="6" r=".9" fill="currentColor"/></symbol>
  <symbol id="i-doc" viewBox="0 0 12 12"><rect x="2" y="1" width="8" height="10" rx=".6" stroke="currentColor" stroke-width="1.1" fill="none"/><path d="M3.8 4h4.4M3.8 6h4.4M3.8 8h3" stroke="currentColor" stroke-width=".9"/></symbol>
  <symbol id="i-screen" viewBox="0 0 12 12"><rect x="1" y="2" width="10" height="7" rx=".6" stroke="currentColor" stroke-width="1.1" fill="none"/><path d="M4 11h4M6 9v2M3 7l2-2 1.5 1L9 4" stroke="currentColor" stroke-width=".9" fill="none"/></symbol>
  <symbol id="i-clock" viewBox="0 0 12 12"><circle cx="6" cy="6" r="4.8" stroke="currentColor" stroke-width="1.1" fill="none"/><path d="M6 3v3l2 1.5" stroke="currentColor" stroke-width="1" fill="none"/></symbol>
  <symbol id="i-pin" viewBox="0 0 12 12"><path d="M6 11S2.5 7 2.5 4.6a3.5 3.5 0 0 1 7 0C9.5 7 6 11 6 11Z" fill="currentColor"/><circle cx="6" cy="4.6" r="1.2" fill="#fff"/></symbol>
  <symbol id="i-phone" viewBox="0 0 12 12"><path d="M3 1.5l2 2.2-1 1.3a7 7 0 0 0 3 3l1.3-1 2.2 2-1.3 1.5C5.5 10.5 1.5 6.5 1.5 2.8Z" fill="currentColor"/></symbol>
  <symbol id="i-mail" viewBox="0 0 12 12"><rect x="1" y="2.5" width="10" height="7" rx=".6" fill="currentColor"/><path d="M1.4 3l4.6 3.5L10.6 3" stroke="#fff" stroke-width=".8" fill="none"/></symbol>
  <symbol id="i-globe" viewBox="0 0 12 12"><circle cx="6" cy="6" r="4.8" stroke="currentColor" stroke-width="1" fill="none"/><ellipse cx="6" cy="6" rx="2" ry="4.8" stroke="currentColor" stroke-width=".8" fill="none"/><path d="M1.2 6h9.6M2 3.5h8M2 8.5h8" stroke="currentColor" stroke-width=".7"/></symbol>
</svg>

<main class="sheet">

<!-- 1 Title dark -->
<section class="slide">
  <div class="bg-city" role="img" aria-label="Dark monochrome city skyline photograph"></div>
  <div class="abs" style="left:0;right:0;top:32px;text-align:center">
    <div class="brand brand-light" style="font-size:7px">VELA CREST</div>
    <div style="color:#fff;font-weight:800;font-size:10.5px;margin-top:8px">POWERPOINT TITLE</div>
    <div style="width:38px;height:.8px;background:var(--red);margin:3px auto"></div>
    <p class="lo-w" style="width:150px;margin:3px auto 0">Lorem ipsum dolor sit amet, consectetuer adipiscing elit. Aenean commodo ligula eget dolor. Aenean massa cum sociis natoque penatibus et magnis dis parturient montes.</p>
    <div class="pill" style="margin-top:5px">Presented By: John Doe</div>
  </div>
</section>

<!-- 2 Title light -->
<section class="slide">
  <div class="abs" style="left:0;right:0;top:40px;height:42px;background:linear-gradient(180deg,#bdbdbf,#f4f4f4)" role="img" aria-label="Faded photograph of a tall office building"></div>
  <svg class="abs" style="left:0;top:0" width="222" height="124" viewBox="0 0 222 124" aria-hidden="true">
    <path d="M0 0H222V44Q111 20 0 44Z" fill="#2e2e30"/>
    <path d="M0 44Q111 20 222 44V52Q160 34 111 34Q62 34 0 52Z" fill="var(--red)"/>
    <rect x="0" y="82" width="222" height="42" fill="#fff"/>
  </svg>
  <div class="brand brand-light abs" style="left:0;right:0;top:10px;text-align:center;font-size:7px">VELA CREST</div>
  <div class="abs" style="left:0;right:0;top:70px;text-align:center">
    <div style="font-weight:800;font-size:9px;color:var(--ink)">POWERPOINT TITLE</div>
    <p class="lo" style="width:150px;margin:2px auto 0">Lorem ipsum dolor sit amet, consectetuer adipiscing elit. Aenean commodo ligula eget dolor. Aenean massa.</p>
    <div class="pill" style="margin-top:3px">Presented By: John Doe</div>
  </div>
</section>

<!-- 3 Title circle -->
<section class="slide">
  <div class="bg-city" role="img" aria-label="Dark monochrome city skyline photograph"></div>
  <div class="abs" style="left:80px;top:12px;width:98px;height:98px;border-radius:50%;border:4px solid #e8e8e8;background:rgba(30,30,32,.55);text-align:center;padding-top:28px">
    <div class="brand brand-light" style="font-size:4px">VELA CREST</div>
    <div style="color:#fff;font-weight:800;font-size:5.8px;margin-top:5px">POWERPOINT TITLE</div>
    <p class="lo-w" style="width:66px;margin:2px auto 0">Lorem ipsum dolor sit amet, adipiscing elit. Aenean commodo.</p>
    <div class="pill" style="margin-top:3px;font-size:2.4px">Presented By: John Doe</div>
  </div>
</section>

<!-- 4 Content -->
<section class="slide">
  <svg class="abs" style="left:0;top:0" width="100" height="124" aria-hidden="true">
    <circle cx="40" cy="60" r="37" fill="none" stroke="var(--red)" stroke-width=".6" stroke-dasharray="1.5 1.2"/>
    <circle cx="40" cy="60" r="32" fill="#333335"/>
  </svg>
  <div class="abs" style="left:14px;top:50px;width:52px;text-align:center">
    <div style="color:#fff;font-weight:800;font-size:7.5px">CONTENT</div>
    <p class="lo-w">Lorem ipsum dolor sit amet, consectetuer adipiscing elit.</p>
  </div>
  <div class="ico ico-fill abs" style="left:61px;top:55px;width:11px;height:11px"><svg><use href="#i-doc"/></svg></div>
  <div class="abs" style="left:84px;top:24px;width:1px;height:72px;background:var(--red)"></div>
  <div class="abs" style="left:81px;top:21px;width:130px">
    <div class="row" style="gap:5px;margin-bottom:5.5px"><span style="width:7px;height:7px;border-radius:50%;border:1.5px solid var(--red);background:#fff;flex:none"></span><div><div class="t">About Our Company</div><p class="lo">Lorem ipsum dolor sit amet, consec adipiscing elit.</p></div></div>
    <div class="row" style="gap:5px;margin-bottom:5.5px"><span style="width:7px;height:7px;border-radius:50%;border:1.5px solid var(--red);background:#fff;flex:none"></span><div><div class="t">What We Do</div><p class="lo">Lorem ipsum dolor sit amet, consec adipiscing elit.</p></div></div>
    <div class="row" style="gap:5px;margin-bottom:5.5px"><span style="width:7px;height:7px;border-radius:50%;border:1.5px solid var(--red);background:#fff;flex:none"></span><div><div class="t">Our Service</div><p class="lo">Lorem ipsum dolor sit amet, consec adipiscing elit.</p></div></div>
    <div class="row" style="gap:5px;margin-bottom:5.5px"><span style="width:7px;height:7px;border-radius:50%;border:1.5px solid var(--red);background:#fff;flex:none"></span><div><div class="t">Our Value</div><p class="lo">Lorem ipsum dolor sit amet, consec adipiscing elit.</p></div></div>
    <div class="row" style="gap:5px"><span style="width:7px;height:7px;border-radius:50%;border:1.5px solid var(--red);background:#fff;flex:none"></span><div><div class="t">Contact Us</div><p class="lo">Lorem ipsum dolor sit amet, consec adipiscing elit.</p></div></div>
  </div>
  <footer class="foot"><span class="pg">4</span><span>Copyright © 2017 Vela Crest | All Rights Reserved</span><span class="brand">VELA CREST</span></footer>
</section>

<!-- 5 About -->
<section class="slide">
  <svg class="abs" style="left:0;top:0" width="222" height="50" viewBox="0 0 222 50" aria-hidden="true">
    <path d="M0 0H222V30Q111 48 0 30Z" fill="#2e2e30"/>
    <path d="M0 30Q111 48 222 30V36Q111 56 0 36Z" fill="var(--red)"/>
  </svg>
  <div class="brand brand-light abs" style="left:0;right:0;top:12px;text-align:center;font-size:7.5px">VELA CREST</div>
  <div class="abs" style="left:18px;right:18px;top:60px;text-align:center">
    <div style="font-weight:700;font-size:5px">About Our Company</div>
    <p class="lo" style="margin-top:3px">Lorem ipsum dolor sit amet, consectetuer adipiscing elit. Aenean commodo ligula eget dolor. Aenean massa. Cum sociis natoque penatibus et magnis dis parturient montes, nascetur ridiculus mus. Donec quam felis, ultricies nec, pellentesque eu, pretium quis, sem.</p>
    <p class="lo" style="margin-top:3px">Aliquam lorem ante, dapibus in, viverra quis, feugiat a, tellus. Phasellus viverra nulla ut metus varius laoreet. Quisque rutrum. Aenean imperdiet. Etiam ultricies nisi vel augue. Curabitur ullamcorper ultricies nisi.</p>
  </div>
  <footer class="foot"><span class="pg">5</span><span>Copyright © 2017 Vela Crest | All Rights Reserved</span><span class="brand">VELA CREST</span></footer>
</section>

<!-- 6 Red block + photo band -->
<section class="slide">
  <div class="band-city" style="height:44px" role="img" aria-label="Dark monochrome city skyline photograph"></div>
  <div class="abs" style="left:8px;top:4px;width:76px;height:98px;background:var(--red);padding:26px 6px 0;color:#fff">
    <div style="font-weight:800;font-size:5.2px;line-height:1.25;text-align:center">Write Something About Your Title or Topic Here</div>
    <p class="lo-w" style="color:#fde;margin-top:3px;text-align:center">Lorem ipsum dolor sit amet, consectetuer adipiscing elit. Aenean commodo ligula eget dolor. Aenean massa cum sociis natoque.</p>
  </div>
  <div class="abs" style="left:96px;top:15px;width:118px">
    <div style="color:#fff;font-weight:700;font-size:4.4px">Vela Crest Powerpoint</div>
    <p class="lo-w">Lorem ipsum dolor sit amet, consectetuer adipiscing elit. Aenean commodo ligula eget dolor.</p>
  </div>
  <div class="abs row" style="left:98px;top:56px;gap:17px;text-align:center">
    <div style="width:26px"><div class="ico" style="margin:0 auto"><svg><use href="#i-target"/></svg></div><div class="t" style="font-size:2.8px;margin-top:3px">Insert Text Here</div><p class="lo">Lorem ipsum dolor sit amet.</p></div>
    <div style="width:26px"><div class="ico" style="margin:0 auto"><svg><use href="#i-bars"/></svg></div><div class="t" style="font-size:2.8px;margin-top:3px">Insert Text Here</div><p class="lo">Lorem ipsum dolor sit amet.</p></div>
    <div style="width:26px"><div class="ico" style="margin:0 auto"><svg><use href="#i-clock"/></svg></div><div class="t" style="font-size:2.8px;margin-top:3px">Insert Text Here</div><p class="lo">Lorem ipsum dolor sit amet.</p></div>
  </div>
  <footer class="foot"><span class="pg">6</span><span>Copyright © 2017 Vela Crest | All Rights Reserved</span><span class="brand">VELA CREST</span></footer>
</section>

<!-- 7 Dark band + four items -->
<section class="slide">
  <div class="hdr">Vela Crest Powerpoint Template</div>
  <div class="abs row" style="left:0;right:0;top:20px;height:38px;background:var(--dark);padding:9px 8px;gap:8px">
    <div style="color:#fff;font-weight:700;font-size:5.2px;line-height:1.2;width:72px">Write Something About Your Title or Topic Here</div>
    <p class="lo-w" style="flex:1">Lorem ipsum dolor sit amet, consectetuer adipiscing elit. Aenean commodo ligula eget dolor. Aenean massa. Cum sociis natoque penatibus et magnis dis parturient montes, nascetur ridiculus mus.</p>
  </div>
  <div class="abs" style="left:10px;top:66px;display:grid;grid-template-columns:100px 100px;gap:5px 12px">
    <div class="row" style="gap:4px"><div class="ico ico-fill" style="flex:none"><svg><use href="#i-target"/></svg></div><div><div class="t" style="font-size:2.8px">Insert text here</div><p class="lo">Lorem ipsum dolor sit amet, consectetuer adipiscing elit.</p></div></div>
    <div class="row" style="gap:4px"><div class="ico ico-fill" style="flex:none"><svg><use href="#i-bars"/></svg></div><div><div class="t" style="font-size:2.8px">Insert text here</div><p class="lo">Lorem ipsum dolor sit amet, consectetuer adipiscing elit.</p></div></div>
    <div class="row" style="gap:4px"><div class="ico ico-fill" style="flex:none"><svg><use href="#i-pie"/></svg></div><div><div class="t" style="font-size:2.8px">Insert text here</div><p class="lo">Lorem ipsum dolor sit amet, consectetuer adipiscing elit.</p></div></div>
    <div class="row" style="gap:4px"><div class="ico ico-fill" style="flex:none"><svg><use href="#i-doc"/></svg></div><div><div class="t" style="font-size:2.8px">Insert text here</div><p class="lo">Lorem ipsum dolor sit amet, consectetuer adipiscing elit.</p></div></div>
  </div>
  <footer class="foot"><span class="pg">7</span><span>Copyright © 2017 Vela Crest | All Rights Reserved</span><span class="brand">VELA CREST</span></footer>
</section>

<!-- 8 Numbered list -->
<section class="slide">
  <div class="hdr">Vela Crest Powerpoint Template</div>
  <div class="abs" style="left:8px;top:22px;display:grid;grid-template-columns:100px 100px;gap:6px 8px">
    <div class="row"><div style="width:15px;height:20px;background:var(--red);color:#fff;font-weight:800;font-size:13px;display:flex;align-items:center;justify-content:center">1</div><div style="flex:1;background:var(--dark);padding:2px 3px"><div class="t" style="color:#fff;font-size:2.8px">Insert text here</div><p class="lo-w">Lorem ipsum dolor sit amet, consectetuer adipiscing elit. Cum sociis natoque.</p></div></div>
    <div class="row"><div style="width:15px;height:20px;background:var(--red);color:#fff;font-weight:800;font-size:13px;display:flex;align-items:center;justify-content:center">4</div><div style="flex:1;background:var(--dark);padding:2px 3px"><div class="t" style="color:#fff;font-size:2.8px">Insert text here</div><p class="lo-w">Lorem ipsum dolor sit amet, consectetuer adipiscing elit. Cum sociis natoque.</p></div></div>
    <div class="row"><div style="width:15px;height:20px;background:var(--red);color:#fff;font-weight:800;font-size:13px;display:flex;align-items:center;justify-content:center">2</div><div style="flex:1;background:var(--dark);padding:2px 3px"><div class="t" style="color:#fff;font-size:2.8px">Insert text here</div><p class="lo-w">Lorem ipsum dolor sit amet, consectetuer adipiscing elit. Cum sociis natoque.</p></div></div>
    <div class="row"><div style="width:15px;height:20px;background:var(--red);color:#fff;font-weight:800;font-size:13px;display:flex;align-items:center;justify-content:center">5</div><div style="flex:1;background:var(--dark);padding:2px 3px"><div class="t" style="color:#fff;font-size:2.8px">Insert text here</div><p class="lo-w">Lorem ipsum dolor sit amet, consectetuer adipiscing elit. Cum sociis natoque.</p></div></div>
    <div class="row"><div style="width:15px;height:20px;background:var(--red);color:#fff;font-weight:800;font-size:13px;display:flex;align-items:center;justify-content:center">3</div><div style="flex:1;background:var(--dark);padding:2px 3px"><div class="t" style="color:#fff;font-size:2.8px">Insert text here</div><p class="lo-w">Lorem ipsum dolor sit amet, consectetuer adipiscing elit. Cum sociis natoque.</p></div></div>
    <div class="row"><div style="width:15px;height:20px;background:var(--red);color:#fff;font-weight:800;font-size:13px;display:flex;align-items:center;justify-content:center">6</div><div style="flex:1;background:var(--dark);padding:2px 3px"><div class="t" style="color:#fff;font-size:2.8px">Insert text here</div><p class="lo-w">Lorem ipsum dolor sit amet, consectetuer adipiscing elit. Cum sociis natoque.</p></div></div>
  </div>
  <footer class="foot"><span class="pg">8</span><span>Copyright © 2017 Vela Crest | All Rights Reserved</span><span class="brand">VELA CREST</span></footer>
</section>

<!-- 9 Four red tiles -->
<section class="slide">
  <div class="hdr">Vela Crest Powerpoint Template</div>
  <div class="abs row" style="left:8px;top:26px;gap:6px">
    <div style="width:47px;text-align:center"><div style="background:var(--red);height:32px;color:#fff;padding-top:5px"><svg width="13" height="13" style="color:#fff"><use href="#i-screen"/></svg><div style="font-size:3px;font-weight:700;margin-top:2px">Insert text here</div></div><div style="background:var(--dark);height:26px;padding:4px 3px"><p class="lo-w">Lorem ipsum dolor sit amet, consectetuer adipiscing elit.</p></div></div>
    <div style="width:47px;text-align:center"><div style="background:var(--red);height:32px;color:#fff;padding-top:5px"><svg width="13" height="13" style="color:#fff"><use href="#i-screen"/></svg><div style="font-size:3px;font-weight:700;margin-top:2px">Insert text here</div></div><div style="background:var(--dark);height:26px;padding:4px 3px"><p class="lo-w">Lorem ipsum dolor sit amet, consectetuer adipiscing elit.</p></div></div>
    <div style="width:47px;text-align:center"><div style="background:var(--red);height:32px;color:#fff;padding-top:5px"><svg width="13" height="13" style="color:#fff"><use href="#i-clock"/></svg><div style="font-size:3px;font-weight:700;margin-top:2px">Insert text here</div></div><div style="background:var(--dark);height:26px;padding:4px 3px"><p class="lo-w">Lorem ipsum dolor sit amet, consectetuer adipiscing elit.</p></div></div>
    <div style="width:47px;text-align:center"><div style="background:var(--red);height:32px;color:#fff;padding-top:5px"><svg width="13" height="13" style="color:#fff"><use href="#i-doc"/></svg><div style="font-size:3px;font-weight:700;margin-top:2px">Insert text here</div></div><div style="background:var(--dark);height:26px;padding:4px 3px"><p class="lo-w">Lorem ipsum dolor sit amet, consectetuer adipiscing elit.</p></div></div>
  </div>
  <footer class="foot"><span class="pg">9</span><span>Copyright © 2017 Vela Crest | All Rights Reserved</span><span class="brand">VELA CREST</span></footer>
</section>

<!-- 10 Arrow process -->
<section class="slide">
  <div class="hdr">Vela Crest Powerpoint Template</div>
  <svg class="abs" style="left:0;top:0" width="222" height="124" viewBox="0 0 222 124" aria-hidden="true">
    <path d="M0 57H40L45 62L40 67H0Z" fill="var(--red)"/>
    <path d="M42 57H84L89 62L84 67H42L47 62Z" fill="#333335"/>
    <path d="M86 57H128L133 62L128 67H86L91 62Z" fill="var(--red)"/>
    <path d="M130 57H172L177 62L172 67H130L135 62Z" fill="#333335"/>
    <path d="M174 57H214L219 62L214 67H174L179 62Z" fill="var(--red)"/>
    <circle cx="42" cy="37" r="7" fill="#333335"/><line x1="42" y1="44" x2="42" y2="57" stroke="#333335" stroke-width=".5"/>
    <circle cx="130" cy="37" r="7" fill="#333335"/><line x1="130" y1="44" x2="130" y2="57" stroke="#333335" stroke-width=".5"/>
    <circle cx="86" cy="87" r="7" fill="#fff" stroke="var(--red)" stroke-width=".8"/><line x1="86" y1="67" x2="86" y2="80" stroke="var(--red)" stroke-width=".5"/>
    <circle cx="174" cy="87" r="7" fill="#fff" stroke="var(--red)" stroke-width=".8"/><line x1="174" y1="67" x2="174" y2="80" stroke="var(--red)" stroke-width=".5"/>
    <use href="#i-bars" x="38" y="33" width="8" height="8" style="color:#fff"/>
    <use href="#i-pie" x="126" y="33" width="8" height="8" style="color:#fff"/>
    <use href="#i-target" x="82" y="83" width="8" height="8" style="color:var(--red)"/>
    <use href="#i-doc" x="170" y="83" width="8" height="8" style="color:var(--red)"/>
  </svg>
  <div class="abs" style="left:68px;top:31px;width:44px"><div class="t" style="font-size:2.8px">Insert Text Here</div><p class="lo">Lorem ipsum dolor sit amet, consectetuer.</p></div>
  <div class="abs" style="left:156px;top:31px;width:44px"><div class="t" style="font-size:2.8px">Insert Text Here</div><p class="lo">Lorem ipsum dolor sit amet, consectetuer.</p></div>
  <div class="abs" style="left:22px;top:82px;width:44px"><div class="t" style="font-size:2.8px">Insert Text Here</div><p class="lo">Lorem ipsum dolor sit amet, consectetuer.</p></div>
  <div class="abs" style="left:112px;top:82px;width:44px"><div class="t" style="font-size:2.8px">Insert Text Here</div><p class="lo">Lorem ipsum dolor sit amet, consectetuer.</p></div>
  <footer class="foot"><span class="pg">10</span><span>Copyright © 2017 Vela Crest | All Rights Reserved</span><span class="brand">VELA CREST</span></footer>
</section>

<!-- 11 Chain -->
<section class="slide">
  <div class="hdr">Vela Crest Powerpoint Template</div>
  <div class="abs row" style="left:32px;top:21px;gap:10px;text-align:center">
    <div style="width:38px"><div class="t" style="font-size:2.8px">Insert Text Here</div><p class="lo">Lorem ipsum dolor sit amet, consectetuer.</p></div>
    <div style="width:38px"><div class="t" style="font-size:2.8px">Insert Text Here</div><p class="lo">Lorem ipsum dolor sit amet, consectetuer.</p></div>
    <div style="width:38px"><div class="t" style="font-size:2.8px">Insert Text Here</div><p class="lo">Lorem ipsum dolor sit amet, consectetuer.</p></div>
  </div>
  <svg class="abs" style="left:0;top:0" width="222" height="124" viewBox="0 0 222 124" aria-hidden="true">
    <rect x="46" y="58" width="130" height="10" fill="#333335"/>
    <circle cx="46" cy="63" r="13" fill="var(--red)"/>
    <circle cx="79" cy="50" r="13" fill="#333335"/>
    <circle cx="112" cy="76" r="13" fill="var(--red)"/>
    <circle cx="145" cy="50" r="13" fill="#333335"/>
    <circle cx="178" cy="63" r="13" fill="var(--red)"/>
    <g fill="#fff"><circle cx="46" cy="63" r="7"/><circle cx="79" cy="50" r="7"/><circle cx="112" cy="76" r="7"/><circle cx="145" cy="50" r="7"/><circle cx="178" cy="63" r="7"/></g>
    <use href="#i-doc" x="42" y="59" width="8" height="8" style="color:var(--red)"/>
    <use href="#i-pie" x="75" y="46" width="8" height="8" style="color:#333"/>
    <use href="#i-target" x="108" y="72" width="8" height="8" style="color:var(--red)"/>
    <use href="#i-bars" x="141" y="46" width="8" height="8" style="color:#333"/>
    <use href="#i-clock" x="174" y="59" width="8" height="8" style="color:var(--red)"/>
  </svg>
  <div class="abs row" style="left:14px;top:92px;gap:8px;text-align:center">
    <div style="width:40px"><div class="t" style="font-size:2.8px">Insert Text Here</div><p class="lo">Lorem ipsum dolor sit amet, consectetuer.</p></div>
    <div style="width:40px"><div class="t" style="font-size:2.8px">Insert Text Here</div><p class="lo">Lorem ipsum dolor sit amet, consectetuer.</p></div>
    <div style="width:40px"><div class="t" style="font-size:2.8px">Insert Text Here</div><p class="lo">Lorem ipsum dolor sit amet, consectetuer.</p></div>
    <div style="width:40px"><div class="t" style="font-size:2.8px">Insert Text Here</div><p class="lo">Lorem ipsum dolor sit amet, consectetuer.</p></div>
  </div>
  <footer class="foot"><span class="pg">11</span><span>Copyright © 2017 Vela Crest | All Rights Reserved</span><span class="brand">VELA CREST</span></footer>
</section>

<!-- 12 Title + red icon column -->
<section class="slide">
  <div class="abs" style="left:8px;top:30px;width:96px">
    <div style="font-weight:700;font-size:5.6px;line-height:1.2;border-left:1.4px solid var(--red);padding-left:3px">Write Something About Your Title or Topic Here</div>
    <p class="lo" style="margin-top:4px">Lorem ipsum dolor sit amet, consectetuer adipiscing elit. Aenean commodo ligula eget dolor. Aenean massa. Cum sociis natoque penatibus et magnis dis parturient montes.</p>
    <p class="lo" style="margin-top:3px">Aliquam lorem ante, dapibus in, viverra quis, feugiat a, tellus. Phasellus viverra nulla ut metus varius laoreet. Quisque rutrum. Aenean imperdiet.</p>
  </div>
  <div class="abs" style="left:114px;top:12px;width:24px;height:96px;background:var(--red);display:flex;flex-direction:column;align-items:center;justify-content:space-around;color:#fff">
    <svg width="10" height="10"><use href="#i-doc"/></svg><svg width="10" height="10"><use href="#i-screen"/></svg><svg width="10" height="10"><use href="#i-bars"/></svg><svg width="10" height="10"><use href="#i-pie"/></svg>
  </div>
  <div class="abs" style="left:146px;top:14px;width:70px;display:flex;flex-direction:column;gap:9px">
    <div><div class="t" style="font-size:2.8px">Insert Text Here</div><p class="lo">Lorem ipsum dolor sit amet, consectetuer adipiscing elit.</p></div>
    <div><div class="t" style="font-size:2.8px">Insert Text Here</div><p class="lo">Lorem ipsum dolor sit amet, consectetuer adipiscing elit.</p></div>
    <div><div class="t" style="font-size:2.8px">Insert Text Here</div><p class="lo">Lorem ipsum dolor sit amet, consectetuer adipiscing elit.</p></div>
    <div><div class="t" style="font-size:2.8px">Insert Text Here</div><p class="lo">Lorem ipsum dolor sit amet, consectetuer adipiscing elit.</p></div>
  </div>
  <footer class="foot"><span class="pg">12</span><span>Copyright © 2017 Vela Crest | All Rights Reserved</span><span class="brand">VELA CREST</span></footer>
</section>

<!-- 13 Grouped bars -->
<section class="slide">
  <div class="hdr">Vela Crest Powerpoint Template</div>
  <svg class="abs" style="left:8px;top:24px" width="110" height="86" viewBox="0 0 110 86" aria-label="Grouped bar chart for January, February and March">
    <g stroke="#ececec" stroke-width=".4"><line x1="10" y1="4" x2="108" y2="4"/><line x1="10" y1="20" x2="108" y2="20"/><line x1="10" y1="36" x2="108" y2="36"/><line x1="10" y1="52" x2="108" y2="52"/><line x1="10" y1="68" x2="108" y2="68"/></g>
    <g font-size="3" fill="#888"><text x="2" y="6">40</text><text x="2" y="22">30</text><text x="2" y="38">20</text><text x="2" y="54">10</text><text x="4" y="70">0</text></g>
    <rect x="16" y="16" width="6" height="52" fill="#3b3b3d"/><rect x="23" y="24" width="6" height="44" fill="var(--red)"/><rect x="30" y="38" width="6" height="30" fill="#d4d4d4"/>
    <rect x="48" y="4" width="6" height="64" fill="#3b3b3d"/><rect x="55" y="30" width="6" height="38" fill="var(--red)"/><rect x="62" y="48" width="6" height="20" fill="#d4d4d4"/>
    <rect x="80" y="12" width="6" height="56" fill="#3b3b3d"/><rect x="87" y="36" width="6" height="32" fill="var(--red)"/><rect x="94" y="48" width="6" height="20" fill="#d4d4d4"/>
    <g font-size="3" fill="#888"><text x="19" y="76">January</text><text x="51" y="76">February</text><text x="85" y="76">March</text></g>
  </svg>
  <div class="abs" style="left:132px;top:32px;width:84px;display:flex;flex-direction:column;gap:7px">
    <div class="row" style="gap:4px"><svg width="9" height="9" style="color:var(--red);flex:none"><use href="#i-bars"/></svg><div><div class="t" style="font-size:2.9px">Insert Text Here</div><p class="lo">Lorem ipsum dolor sit amet, consectetuer adipiscing elit.</p></div></div>
    <div class="row" style="gap:4px"><svg width="9" height="9" style="color:var(--red);flex:none"><use href="#i-clock"/></svg><div><div class="t" style="font-size:2.9px">Insert Text Here</div><p class="lo">Lorem ipsum dolor sit amet, consectetuer adipiscing elit.</p></div></div>
    <div class="row" style="gap:4px"><svg width="9" height="9" style="color:var(--red);flex:none"><use href="#i-doc"/></svg><div><div class="t" style="font-size:2.9px">Insert Text Here</div><p class="lo">Lorem ipsum dolor sit amet, consectetuer adipiscing elit.</p></div></div>
  </div>
  <footer class="foot"><span class="pg">13</span><span>Copyright © 2017 Vela Crest | All Rights Reserved</span><span class="brand">VELA CREST</span></footer>
</section>

<!-- 14 Monthly bars -->
<section class="slide">
  <div class="hdr">Vela Crest Powerpoint Template</div>
  <svg class="abs" style="left:10px;top:20px" width="202" height="62" viewBox="0 0 202 62" aria-label="Monthly bar chart rising from January to December">
    <g font-size="2.2" fill="#fff" text-anchor="middle">
      <rect x="4" y="48" width="8" height="6" fill="#d9d9d9"/><text x="8" y="52">1</text>
      <rect x="20" y="46" width="8" height="8" fill="#cfcfcf"/><text x="24" y="50">2</text>
      <rect x="36" y="42" width="8" height="12" fill="#bdbdbd"/><text x="40" y="46">3</text>
      <rect x="52" y="40" width="8" height="14" fill="#a8a8a8"/><text x="56" y="44">4</text>
      <rect x="68" y="36" width="8" height="18" fill="#8e8e8e"/><text x="72" y="40">5</text>
      <rect x="84" y="34" width="8" height="20" fill="#6e6e6e"/><text x="88" y="38">6</text>
      <rect x="100" y="30" width="8" height="24" fill="#505052"/><text x="104" y="34">7</text>
      <rect x="116" y="26" width="8" height="28" fill="#3b3b3d"/><text x="120" y="30">8</text>
      <rect x="132" y="20" width="8" height="34" fill="var(--red)"/><text x="136" y="24">9</text>
      <rect x="148" y="12" width="8" height="42" fill="var(--red)"/><text x="152" y="16">10</text>
      <rect x="164" y="4" width="8" height="50" fill="var(--red)"/><text x="168" y="8">11</text>
      <rect x="180" y="10" width="8" height="44" fill="var(--red)"/><text x="184" y="14">12</text>
    </g>
    <line x1="0" y1="54" x2="196" y2="54" stroke="#ddd" stroke-width=".4"/>
    <g font-size="2.4" fill="#888" text-anchor="middle"><text x="8" y="59">Jan</text><text x="24" y="59">Feb</text><text x="40" y="59">Mar</text><text x="56" y="59">Apr</text><text x="72" y="59">May</text><text x="88" y="59">Jun</text><text x="104" y="59">Jul</text><text x="120" y="59">Aug</text><text x="136" y="59">Sep</text><text x="152" y="59">Oct</text><text x="168" y="59">Nov</text><text x="184" y="59">Dec</text></g>
  </svg>
  <p class="lo abs" style="left:18px;right:18px;top:88px;text-align:center">Lorem ipsum dolor sit amet, consectetuer adipiscing elit. Aenean commodo ligula eget dolor. Aenean massa. Cum sociis natoque penatibus et magnis dis parturient montes, nascetur ridiculus mus. Donec quam felis, ultricies nec, pellentesque eu, pretium quis, sem.</p>
  <footer class="foot"><span class="pg">14</span><span>Copyright © 2017 Vela Crest | All Rights Reserved</span><span class="brand">VELA CREST</span></footer>
</section>

<!-- 15 Donuts -->
<section class="slide">
  <div class="hdr">Vela Crest Powerpoint Template</div>
  <svg class="abs" style="left:8px;top:30px" width="206" height="40" viewBox="0 0 206 40" aria-label="Four donut charts: 85, 68, 45 and 74 percent">
    <g fill="none" stroke-width="5">
      <circle cx="26" cy="20" r="16" stroke="#3b3b3d"/><circle cx="26" cy="20" r="16" stroke="var(--red)" pathLength="100" stroke-dasharray="85 100" transform="rotate(-90 26 20)"/>
      <circle cx="77" cy="20" r="16" stroke="#3b3b3d"/><circle cx="77" cy="20" r="16" stroke="var(--red)" pathLength="100" stroke-dasharray="68 100" transform="rotate(-90 77 20)"/>
      <circle cx="128" cy="20" r="16" stroke="#3b3b3d"/><circle cx="128" cy="20" r="16" stroke="var(--red)" pathLength="100" stroke-dasharray="45 100" transform="rotate(-90 128 20)"/>
      <circle cx="179" cy="20" r="16" stroke="#3b3b3d"/><circle cx="179" cy="20" r="16" stroke="var(--red)" pathLength="100" stroke-dasharray="74 100" transform="rotate(-90 179 20)"/>
    </g>
    <g font-size="6" font-weight="700" fill="#3b3b3d" text-anchor="middle" font-family="Open Sans, sans-serif"><text x="26" y="22.5">85%</text><text x="77" y="22.5">68%</text><text x="128" y="22.5">45%</text><text x="179" y="22.5">74%</text></g>
  </svg>
  <div class="abs row" style="left:12px;top:74px;gap:11px;text-align:center">
    <div style="width:40px"><div class="t">Market Data</div><p class="lo">Lorem ipsum dolor sit amet, consectetuer adipiscing elit.</p></div>
    <div style="width:40px"><div class="t">Market Data</div><p class="lo">Lorem ipsum dolor sit amet, consectetuer adipiscing elit.</p></div>
    <div style="width:40px"><div class="t">Market Data</div><p class="lo">Lorem ipsum dolor sit amet, consectetuer adipiscing elit.</p></div>
    <div style="width:40px"><div class="t">Market Data</div><p class="lo">Lorem ipsum dolor sit amet, consectetuer adipiscing elit.</p></div>
  </div>
  <footer class="foot"><span class="pg">15</span><span>Copyright © 2017 Vela Crest | All Rights Reserved</span><span class="brand">VELA CREST</span></footer>
</section>

<!-- 16 Full table -->
<section class="slide">
  <div class="hdr">Vela Crest Powerpoint Template</div>
  <div class="abs" style="left:8px;right:8px;top:20px">
    <table>
      <tr><th>Item Description</th><th>Number</th><th>Number</th><th>Text Title</th><th>Text Title</th></tr>
      <tr><td>Lorem Ipsum</td><td>4.3</td><td>4.2</td><td>Important Data Analysis</td><td>Yes</td></tr>
      <tr><td>Lorem Ipsum</td><td>4.1</td><td>4.4</td><td>Important Data Analysis</td><td>No</td></tr>
      <tr><td>Lorem Ipsum</td><td>3.3</td><td>3.5</td><td>Important Data Analysis</td><td>Yes</td></tr>
      <tr><td>Lorem Ipsum</td><td>2.1</td><td>2.8</td><td>Important Data Analysis</td><td>Yes</td></tr>
      <tr><td>Lorem Ipsum</td><td>1.7</td><td>1.5</td><td>Important Data Analysis</td><td>Yes</td></tr>
      <tr class="tbl-foot"><td></td><td></td><td></td><td></td><td></td></tr>
    </table>
    <p class="lo" style="margin-top:4px;text-align:center">Lorem ipsum dolor sit amet, consectetuer adipiscing elit. Aenean commodo ligula eget dolor. Aenean massa. Cum sociis natoque penatibus et magnis dis parturient montes, nascetur ridiculus mus. Donec quam felis.</p>
  </div>
  <footer class="foot"><span class="pg">16</span><span>Copyright © 2017 Vela Crest | All Rights Reserved</span><span class="brand">VELA CREST</span></footer>
</section>

<!-- 17 Two tables -->
<section class="slide">
  <div class="hdr">Vela Crest Powerpoint Template</div>
  <div class="abs row" style="left:8px;right:8px;top:20px;gap:8px">
    <div style="flex:1">
      <table><tr><th>Item Description</th><th>Number</th><th>Text Title</th><th>Text Title</th></tr>
        <tr><td>Lorem Ipsum</td><td>4.3</td><td>Data Analysis</td><td>Yes</td></tr><tr><td>Lorem Ipsum</td><td>4.1</td><td>Data Analysis</td><td>No</td></tr><tr><td>Lorem Ipsum</td><td>3.3</td><td>Data Analysis</td><td>Yes</td></tr><tr><td>Lorem Ipsum</td><td>2.1</td><td>Data Analysis</td><td>Yes</td></tr><tr><td>Lorem Ipsum</td><td>1.7</td><td>Data Analysis</td><td>Yes</td></tr><tr class="tbl-foot"><td></td><td></td><td></td><td></td></tr></table>
      <div class="t" style="font-size:2.8px;margin-top:3px">Insert Text Here</div><p class="lo">Lorem ipsum dolor sit amet, consectetuer adipiscing elit. Aenean commodo ligula eget dolor.</p>
    </div>
    <div style="flex:1">
      <table><tr><th>Item Description</th><th>Number</th><th>Text Title</th><th>Text Title</th></tr>
        <tr><td>Lorem Ipsum</td><td>4.3</td><td>Data Analysis</td><td>Yes</td></tr><tr><td>Lorem Ipsum</td><td>4.1</td><td>Data Analysis</td><td>No</td></tr><tr><td>Lorem Ipsum</td><td>3.3</td><td>Data Analysis</td><td>Yes</td></tr><tr><td>Lorem Ipsum</td><td>2.1</td><td>Data Analysis</td><td>Yes</td></tr><tr><td>Lorem Ipsum</td><td>1.7</td><td>Data Analysis</td><td>Yes</td></tr><tr class="tbl-foot"><td></td><td></td><td></td><td></td></tr></table>
      <div class="t" style="font-size:2.8px;margin-top:3px">Insert Text Here</div><p class="lo">Lorem ipsum dolor sit amet, consectetuer adipiscing elit. Aenean commodo ligula eget dolor.</p>
    </div>
  </div>
  <footer class="foot"><span class="pg">17</span><span>Copyright © 2017 Vela Crest | All Rights Reserved</span><span class="brand">VELA CREST</span></footer>
</section>

<!-- 18 Table + notes -->
<section class="slide">
  <div class="hdr">Vela Crest Powerpoint Template</div>
  <div class="abs" style="left:8px;top:20px;width:120px">
    <table><tr><th>Item Description</th><th>Number</th><th>Text Title</th><th>Text Title</th></tr>
      <tr><td>Lorem Ipsum</td><td>4.3</td><td>Data Analysis</td><td>Yes</td></tr><tr><td>Lorem Ipsum</td><td>4.1</td><td>Data Analysis</td><td>No</td></tr><tr><td>Lorem Ipsum</td><td>3.3</td><td>Data Analysis</td><td>Yes</td></tr><tr><td>Lorem Ipsum</td><td>2.1</td><td>Data Analysis</td><td>Yes</td></tr><tr><td>Lorem Ipsum</td><td>1.7</td><td>Data Analysis</td><td>Yes</td></tr><tr class="tbl-foot"><td></td><td></td><td></td><td></td></tr></table>
  </div>
  <div class="abs" style="left:136px;top:24px;width:80px">
    <div style="font-weight:700;font-size:4.4px;line-height:1.2">Write Something About Your Title or Topic Here</div>
    <p class="lo" style="margin-top:2px">Lorem ipsum dolor sit amet, consectetuer adipiscing elit.</p>
    <div style="display:flex;flex-direction:column;gap:4px;margin-top:5px">
      <div class="row" style="gap:3px"><div class="ico ico-fill" style="flex:none;width:8px;height:8px"><svg><use href="#i-bars"/></svg></div><div><div class="t" style="font-size:2.8px">Insert Text Here</div><p class="lo">Lorem ipsum dolor sit amet, consectetuer.</p></div></div>
      <div class="row" style="gap:3px"><div class="ico ico-dark" style="flex:none;width:8px;height:8px"><svg><use href="#i-pie"/></svg></div><div><div class="t" style="font-size:2.8px">Insert Text Here</div><p class="lo">Lorem ipsum dolor sit amet, consectetuer.</p></div></div>
      <div class="row" style="gap:3px"><div class="ico" style="flex:none;width:8px;height:8px;background:#888;border:none;color:#fff"><svg><use href="#i-doc"/></svg></div><div><div class="t" style="font-size:2.8px">Insert Text Here</div><p class="lo">Lorem ipsum dolor sit amet, consectetuer.</p></div></div>
    </div>
  </div>
  <footer class="foot"><span class="pg">18</span><span>Copyright © 2017 Vela Crest | All Rights Reserved</span><span class="brand">VELA CREST</span></footer>
</section>

<!-- 19 Six icon features -->
<section class="slide">
  <div class="hdr">Vela Crest Powerpoint Template</div>
  <div class="abs" style="left:12px;top:22px;display:grid;grid-template-columns:repeat(3,60px);gap:8px 8px;text-align:center;color:var(--red)">
    <div><svg width="11" height="11"><use href="#i-target"/></svg><div class="t" style="font-size:2.8px">Insert Text Here</div><p class="lo">Lorem ipsum dolor sit amet, consectetuer adipiscing elit. Aenean commodo.</p></div>
    <div><svg width="11" height="11"><use href="#i-bars"/></svg><div class="t" style="font-size:2.8px">Insert Text Here</div><p class="lo">Lorem ipsum dolor sit amet, consectetuer adipiscing elit. Aenean commodo.</p></div>
    <div><svg width="11" height="11"><use href="#i-screen"/></svg><div class="t" style="font-size:2.8px">Insert Text Here</div><p class="lo">Lorem ipsum dolor sit amet, consectetuer adipiscing elit. Aenean commodo.</p></div>
    <div><svg width="11" height="11"><use href="#i-pie"/></svg><div class="t" style="font-size:2.8px">Insert Text Here</div><p class="lo">Lorem ipsum dolor sit amet, consectetuer adipiscing elit. Aenean commodo.</p></div>
    <div><svg width="11" height="11"><use href="#i-doc"/></svg><div class="t" style="font-size:2.8px">Insert Text Here</div><p class="lo">Lorem ipsum dolor sit amet, consectetuer adipiscing elit. Aenean commodo.</p></div>
    <div><svg width="11" height="11"><use href="#i-clock"/></svg><div class="t" style="font-size:2.8px">Insert Text Here</div><p class="lo">Lorem ipsum dolor sit amet, consectetuer adipiscing elit. Aenean commodo.</p></div>
  </div>
  <footer class="foot"><span class="pg">19</span><span>Copyright © 2017 Vela Crest | All Rights Reserved</span><span class="brand">VELA CREST</span></footer>
</section>

<!-- 20 Four circles + CTA -->
<section class="slide">
  <div class="hdr">Vela Crest Powerpoint Template</div>
  <div class="abs row" style="left:14px;top:26px;gap:8px;text-align:center">
    <div style="width:44px"><div class="ico" style="width:16px;height:16px;margin:0 auto;border-color:#555;color:var(--red)"><svg style="width:8px;height:8px"><use href="#i-bars"/></svg></div><div class="t" style="font-size:2.8px;margin-top:4px">Title Text Demo</div><p class="lo">Lorem ipsum dolor sit amet, consectetuer adipiscing elit.</p></div>
    <div style="width:44px"><div class="ico" style="width:16px;height:16px;margin:0 auto;border-color:#555;color:var(--red)"><svg style="width:8px;height:8px"><use href="#i-target"/></svg></div><div class="t" style="font-size:2.8px;margin-top:4px">Title Text Demo</div><p class="lo">Lorem ipsum dolor sit amet, consectetuer adipiscing elit.</p></div>
    <div style="width:44px"><div class="ico" style="width:16px;height:16px;margin:0 auto;border-color:#555;color:var(--red)"><svg style="width:8px;height:8px"><use href="#i-pie"/></svg></div><div class="t" style="font-size:2.8px;margin-top:4px">Title Text Demo</div><p class="lo">Lorem ipsum dolor sit amet, consectetuer adipiscing elit.</p></div>
    <div style="width:44px"><div class="ico" style="width:16px;height:16px;margin:0 auto;border-color:#555;color:var(--red)"><svg style="width:8px;height:8px"><use href="#i-doc"/></svg></div><div class="t" style="font-size:2.8px;margin-top:4px">Title Text Demo</div><p class="lo">Lorem ipsum dolor sit amet, consectetuer adipiscing elit.</p></div>
  </div>
  <div class="abs" style="left:36px;right:36px;top:86px;background:var(--red);color:#fff;text-align:center;font-weight:700;font-size:4px;padding:2px 0;border-radius:5px">Try a New Experience And Never Stop</div>
  <footer class="foot"><span class="pg">20</span><span>Copyright © 2017 Vela Crest | All Rights Reserved</span><span class="brand">VELA CREST</span></footer>
</section>

<!-- 21 Cycle -->
<section class="slide">
  <div class="hdr">Vela Crest Powerpoint Template</div>
  <svg class="abs" style="left:81px;top:26px" width="60" height="60" viewBox="0 0 60 60" aria-label="Cycle diagram of eight segments around a central hub">
    <g fill="none" stroke-width="14" transform="rotate(-90 30 30)">
      <circle cx="30" cy="30" r="22" stroke="#3b3b3d" pathLength="100" stroke-dasharray="11.5 88.5"/>
      <circle cx="30" cy="30" r="22" stroke="#6b6b6d" pathLength="100" stroke-dasharray="11.5 88.5" stroke-dashoffset="-12.5"/>
      <circle cx="30" cy="30" r="22" stroke="#3b3b3d" pathLength="100" stroke-dasharray="11.5 88.5" stroke-dashoffset="-25"/>
      <circle cx="30" cy="30" r="22" stroke="#6b6b6d" pathLength="100" stroke-dasharray="11.5 88.5" stroke-dashoffset="-37.5"/>
      <circle cx="30" cy="30" r="22" stroke="#3b3b3d" pathLength="100" stroke-dasharray="11.5 88.5" stroke-dashoffset="-50"/>
      <circle cx="30" cy="30" r="22" stroke="#6b6b6d" pathLength="100" stroke-dasharray="11.5 88.5" stroke-dashoffset="-62.5"/>
      <circle cx="30" cy="30" r="22" stroke="#3b3b3d" pathLength="100" stroke-dasharray="11.5 88.5" stroke-dashoffset="-75"/>
      <circle cx="30" cy="30" r="22" stroke="#6b6b6d" pathLength="100" stroke-dasharray="11.5 88.5" stroke-dashoffset="-87.5"/>
    </g>
    <polygon points="30,17 41,23.5 41,36.5 30,43 19,36.5 19,23.5" fill="var(--red)"/>
    <text x="30" y="31" font-size="2.6" font-weight="600" fill="#fff" text-anchor="middle" letter-spacing=".3" font-family="Open Sans, sans-serif">VELA CREST</text>
  </svg>
  <div class="abs" style="left:8px;top:22px;width:68px;text-align:right;display:flex;flex-direction:column;gap:7px">
    <div><div class="t t-red" style="font-size:2.8px">Insert Text Here</div><p class="lo">Lorem ipsum dolor sit amet, consectetuer adipiscing elit.</p></div>
    <div><div class="t t-red" style="font-size:2.8px">Insert Text Here</div><p class="lo">Lorem ipsum dolor sit amet, consectetuer adipiscing elit.</p></div>
    <div><div class="t t-red" style="font-size:2.8px">Insert Text Here</div><p class="lo">Lorem ipsum dolor sit amet, consectetuer adipiscing elit.</p></div>
  </div>
  <div class="abs" style="left:146px;top:22px;width:68px;display:flex;flex-direction:column;gap:7px">
    <div><div class="t t-red" style="font-size:2.8px">Insert Text Here</div><p class="lo">Lorem ipsum dolor sit amet, consectetuer adipiscing elit.</p></div>
    <div><div class="t t-red" style="font-size:2.8px">Insert Text Here</div><p class="lo">Lorem ipsum dolor sit amet, consectetuer adipiscing elit.</p></div>
    <div><div class="t t-red" style="font-size:2.8px">Insert Text Here</div><p class="lo">Lorem ipsum dolor sit amet, consectetuer adipiscing elit.</p></div>
  </div>
  <footer class="foot"><span class="pg">21</span><span>Copyright © 2017 Vela Crest | All Rights Reserved</span><span class="brand">VELA CREST</span></footer>
</section>

<!-- 22 Laptop -->
<section class="slide">
  <div class="band-city" style="height:58px" role="img" aria-label="Dark monochrome city skyline photograph"></div>
  <svg class="abs" style="left:14px;top:8px" width="62" height="50" viewBox="0 0 62 50" aria-label="Laptop showing a bar chart">
    <rect x="6" y="2" width="50" height="38" rx="2" fill="#1f1f21"/><rect x="9" y="5" width="44" height="32" fill="#fff"/>
    <rect x="15" y="12" width="4" height="20" fill="#3b3b3d"/><rect x="20" y="18" width="4" height="14" fill="var(--red)"/><rect x="29" y="10" width="4" height="22" fill="#3b3b3d"/><rect x="34" y="20" width="4" height="12" fill="var(--red)"/><rect x="43" y="14" width="4" height="18" fill="#3b3b3d"/><rect x="48" y="22" width="4" height="10" fill="#d4d4d4"/>
    <path d="M0 41H62L58 45H4Z" fill="#bdbdbd"/>
  </svg>
  <div class="abs" style="left:96px;top:8px;width:2px;height:22px;background:var(--red)"></div>
  <div class="abs" style="left:102px;top:8px;width:112px">
    <div style="color:#fff;font-weight:700;font-size:5px;line-height:1.2">Write Something About Your Title or Topic Here</div>
    <p class="lo-w" style="margin-top:2px">Lorem ipsum dolor sit amet, consectetuer adipiscing elit. Aenean commodo ligula eget dolor. Aenean massa.</p>
  </div>
  <div class="abs row" style="left:14px;top:70px;gap:16px;text-align:center">
    <div style="width:38px"><div class="ico" style="margin:0 auto"><svg><use href="#i-target"/></svg></div><div class="t" style="font-size:2.8px;margin-top:3px">Insert Text Here</div><p class="lo">Lorem ipsum dolor sit amet.</p></div>
    <div style="width:38px"><div class="ico" style="margin:0 auto"><svg><use href="#i-bars"/></svg></div><div class="t" style="font-size:2.8px;margin-top:3px">Insert Text Here</div><p class="lo">Lorem ipsum dolor sit amet.</p></div>
    <div style="width:38px"><div class="ico" style="margin:0 auto"><svg><use href="#i-pie"/></svg></div><div class="t" style="font-size:2.8px;margin-top:3px">Insert Text Here</div><p class="lo">Lorem ipsum dolor sit amet.</p></div>
    <div style="width:38px"><div class="ico" style="margin:0 auto"><svg><use href="#i-doc"/></svg></div><div class="t" style="font-size:2.8px;margin-top:3px">Insert Text Here</div><p class="lo">Lorem ipsum dolor sit amet.</p></div>
  </div>
  <footer class="foot"><span class="pg">22</span><span>Copyright © 2017 Vela Crest | All Rights Reserved</span><span class="brand">VELA CREST</span></footer>
</section>

<!-- 23 Monitor -->
<section class="slide">
  <div class="band-city" style="height:48px" role="img" aria-label="Dark monochrome city skyline photograph"></div>
  <svg class="abs" style="left:8px;top:14px" width="72" height="82" viewBox="0 0 72 82" aria-label="Desktop monitor showing a 68 percent donut chart">
    <rect x="0" y="0" width="72" height="54" rx="2" fill="#1f1f21"/><rect x="3" y="3" width="66" height="44" fill="#fff"/>
    <circle cx="18" cy="25" r="9" fill="none" stroke="#3b3b3d" stroke-width="3.5"/>
    <circle cx="18" cy="25" r="9" fill="none" stroke="var(--red)" stroke-width="3.5" pathLength="100" stroke-dasharray="68 100" transform="rotate(-90 18 25)"/>
    <text x="18" y="26.5" font-size="4" text-anchor="middle" font-weight="700" fill="#3b3b3d" font-family="Open Sans, sans-serif">68%</text>
    <text x="33" y="20" font-size="2.6" font-weight="700" fill="#3b3b3d" font-family="Open Sans, sans-serif">Insert Text Here</text>
    <rect x="33" y="23" width="30" height=".8" fill="#bbb"/><rect x="33" y="26" width="28" height=".8" fill="#bbb"/><rect x="33" y="29" width="24" height=".8" fill="#bbb"/>
    <rect x="0" y="50" width="72" height="4" fill="#d0d0d0"/>
    <path d="M30 54H42L44 66H28Z" fill="#bdbdbd"/><rect x="22" y="66" width="28" height="2" rx="1" fill="#a9a9a9"/>
  </svg>
  <div class="abs" style="left:96px;top:10px;width:118px">
    <div style="color:#fff;font-weight:700;font-size:4.6px;border-left:1.4px solid var(--red);padding-left:3px">Vela Crest Powerpoint</div>
    <p class="lo-w" style="margin-top:2px">Lorem ipsum dolor sit amet, consectetuer adipiscing elit. Aenean commodo ligula eget dolor.</p>
  </div>
  <div class="abs" style="left:100px;top:54px;width:112px;display:flex;flex-direction:column;gap:4px">
    <div class="row" style="gap:4px"><div class="ico ico-dark" style="flex:none;width:8px;height:8px"><svg><use href="#i-bars"/></svg></div><div><div class="t" style="font-size:2.8px">Insert Text Here</div><p class="lo">Lorem ipsum dolor sit amet, consectetuer adipiscing elit.</p></div></div>
    <div class="row" style="gap:4px"><div class="ico ico-dark" style="flex:none;width:8px;height:8px"><svg><use href="#i-pie"/></svg></div><div><div class="t" style="font-size:2.8px">Insert Text Here</div><p class="lo">Lorem ipsum dolor sit amet, consectetuer adipiscing elit.</p></div></div>
    <div class="row" style="gap:4px"><div class="ico ico-dark" style="flex:none;width:8px;height:8px"><svg><use href="#i-doc"/></svg></div><div><div class="t" style="font-size:2.8px">Insert Text Here</div><p class="lo">Lorem ipsum dolor sit amet, consectetuer adipiscing elit.</p></div></div>
  </div>
  <footer class="foot"><span class="pg">23</span><span>Copyright © 2017 Vela Crest | All Rights Reserved</span><span class="brand">VELA CREST</span></footer>
</section>

<!-- 24 Tablet -->
<section class="slide">
  <div class="band-city" style="height:44px" role="img" aria-label="Dark monochrome city skyline photograph"></div>
  <svg class="abs" style="left:14px;top:8px" width="58" height="80" viewBox="0 0 58 80" aria-label="Tablet showing a bar chart">
    <rect x="0" y="0" width="58" height="80" rx="4" fill="#1f1f21"/><rect x="4" y="6" width="50" height="66" fill="#fff"/>
    <rect x="10" y="16" width="4" height="20" fill="#3b3b3d"/><rect x="15" y="22" width="4" height="14" fill="var(--red)"/><rect x="20" y="28" width="4" height="8" fill="#d4d4d4"/>
    <rect x="27" y="12" width="4" height="24" fill="#3b3b3d"/><rect x="32" y="24" width="4" height="12" fill="var(--red)"/><rect x="37" y="28" width="4" height="8" fill="#d4d4d4"/>
    <rect x="44" y="18" width="4" height="18" fill="#3b3b3d"/><rect x="49" y="26" width="3" height="10" fill="var(--red)"/>
    <text x="29" y="48" font-size="2.6" font-weight="700" text-anchor="middle" fill="#3b3b3d" font-family="Open Sans, sans-serif">Insert Text Here</text>
    <rect x="10" y="51" width="38" height=".8" fill="#bbb"/><rect x="12" y="54" width="34" height=".8" fill="#bbb"/><rect x="14" y="57" width="30" height=".8" fill="#bbb"/>
    <circle cx="29" cy="76" r="1.6" fill="#555"/>
  </svg>
  <div class="abs" style="left:92px;top:8px;width:122px">
    <div style="color:#fff;font-weight:700;font-size:5px;line-height:1.2;border-left:1.4px solid var(--red);padding-left:3px">Write Something About Your Title or Topic Here</div>
    <p class="lo-w" style="margin-top:2px">Lorem ipsum dolor sit amet, consectetuer adipiscing elit. Aenean commodo ligula eget dolor.</p>
  </div>
  <div class="abs" style="left:96px;top:56px;display:grid;grid-template-columns:56px 56px;gap:6px 6px">
    <div class="row" style="gap:3px"><div class="ico" style="flex:none;width:8px;height:8px"><svg><use href="#i-target"/></svg></div><div><div class="t" style="font-size:2.8px">Insert Text Here</div><p class="lo">Lorem ipsum dolor sit amet.</p></div></div>
    <div class="row" style="gap:3px"><div class="ico" style="flex:none;width:8px;height:8px"><svg><use href="#i-bars"/></svg></div><div><div class="t" style="font-size:2.8px">Insert Text Here</div><p class="lo">Lorem ipsum dolor sit amet.</p></div></div>
    <div class="row" style="gap:3px"><div class="ico" style="flex:none;width:8px;height:8px"><svg><use href="#i-pie"/></svg></div><div><div class="t" style="font-size:2.8px">Insert Text Here</div><p class="lo">Lorem ipsum dolor sit amet.</p></div></div>
    <div class="row" style="gap:3px"><div class="ico" style="flex:none;width:8px;height:8px"><svg><use href="#i-doc"/></svg></div><div><div class="t" style="font-size:2.8px">Insert Text Here</div><p class="lo">Lorem ipsum dolor sit amet.</p></div></div>
  </div>
  <footer class="foot"><span class="pg">24</span><span>Copyright © 2017 Vela Crest | All Rights Reserved</span><span class="brand">VELA CREST</span></footer>
</section>

<!-- 25 Section break -->
<section class="slide">
  <div class="bg-city" role="img" aria-label="Dark monochrome city skyline photograph"></div>
  <div class="abs" style="left:0;right:0;top:42px;text-align:center">
    <div class="brand brand-light" style="font-size:7px">VELA CREST</div>
    <div style="color:#fff;font-weight:800;font-size:12px;margin-top:5px">SECTION BREAK</div>
    <p class="lo-w" style="width:190px;margin:5px auto 0">Lorem ipsum dolor sit amet, consectetuer adipiscing elit. Aenean commodo ligula eget dolor. Aenean massa. Cum sociis natoque penatibus et magnis dis parturient montes, nascetur ridiculus mus. Donec quam felis, ultricies nec, pellentesque eu, pretium quis, sem.</p>
  </div>
</section>

<!-- 26 Contact split -->
<section class="slide">
  <div class="abs" style="left:118px;top:0;right:0;bottom:0;background:linear-gradient(180deg,#5a5a5c,#262628)" role="img" aria-label="Dark monochrome city skyline photograph"></div>
  <div class="brand brand-light abs" style="left:118px;right:0;top:58px;text-align:center;font-size:6px">VELA CREST</div>
  <div class="abs" style="left:10px;top:16px;width:104px">
    <div style="font-weight:800;font-size:7px">CONTACT US</div>
    <p class="lo" style="margin-top:3px">Thank you for taking the time to go through this business profile. If there are any questions or comments, please feel free to contact us.</p>
    <div style="display:flex;flex-direction:column;gap:5px;margin-top:7px;font-size:2.8px">
      <div class="row" style="gap:4px;align-items:center"><div class="ico ico-fill" style="width:8px;height:8px"><svg><use href="#i-pin"/></svg></div><b>Address</b><span>: Company Address</span></div>
      <div class="row" style="gap:4px;align-items:center"><div class="ico ico-fill" style="width:8px;height:8px"><svg><use href="#i-phone"/></svg></div><b>Phone</b><span>: +12 555 014 788</span></div>
      <div class="row" style="gap:4px;align-items:center"><div class="ico ico-fill" style="width:8px;height:8px"><svg><use href="#i-mail"/></svg></div><b>Email</b><span>: support@velacrest.example</span></div>
      <div class="row" style="gap:4px;align-items:center"><div class="ico ico-fill" style="width:8px;height:8px"><svg><use href="#i-globe"/></svg></div><b>Website</b><span>: www.velacrest.example</span></div>
    </div>
  </div>
</section>

<!-- 27 Contact dark -->
<section class="slide">
  <div class="bg-city" role="img" aria-label="Dark monochrome city skyline photograph"></div>
  <div class="abs" style="left:0;right:0;top:20px;text-align:center;color:#fff">
    <div style="font-weight:800;font-size:8px">CONTACT US</div>
    <div class="brand brand-light" style="font-size:6.5px;margin-top:4px">VELA CREST</div>
    <p class="lo-w" style="width:170px;margin:4px auto 0">Thank you for taking the time to go through this business profile. If there are any questions or comments, please feel free to contact us via any method listed below.</p>
  </div>
  <div class="abs row" style="left:10px;right:10px;top:76px;justify-content:space-between;text-align:center;color:#fff;font-size:2.6px">
    <div style="width:48px"><div class="ico" style="margin:0 auto;border-color:#fff;color:#fff;width:11px;height:11px"><svg><use href="#i-pin"/></svg></div><b style="display:block;margin-top:2px">Address</b>Company Address</div>
    <div style="width:48px"><div class="ico" style="margin:0 auto;border-color:#fff;color:#fff;width:11px;height:11px"><svg><use href="#i-phone"/></svg></div><b style="display:block;margin-top:2px">Phone</b>+12 555 014 788</div>
    <div style="width:48px"><div class="ico" style="margin:0 auto;border-color:#fff;color:#fff;width:11px;height:11px"><svg><use href="#i-mail"/></svg></div><b style="display:block;margin-top:2px">Email</b>support@velacrest.example</div>
    <div style="width:48px"><div class="ico" style="margin:0 auto;border-color:#fff;color:#fff;width:11px;height:11px"><svg><use href="#i-globe"/></svg></div><b style="display:block;margin-top:2px">Website</b>www.velacrest.example</div>
  </div>
</section>

</main>
</body>
</html>
```